Letterhead Design for Law Firm

**Edit: I have added the photo of a bottom that I like.

------
We are looking for a re-design of our new letterhead. The letterhead is for a law firm and will be used for digital and traditionally printed correspondence.

Here are some suggestions:

- Please use colours are #8ec900 and simple black.
- Please do not use any type of "waves" at the bottom of the page. This is not in style at all.
- Please stay modern yet conservative.
- Please use font Segoe UI Light or similar if you can
- Avoid clipart or illustrations.
- Utilize ample white space in the layout so the design looks clean and information is easy to read at a glance. Don't overcrowd the letterhead.
- Make sure the letterhead design is consistent with our brand identity (see corvelith.ca)
-Please, no black headers or footers.

I am attaching my current letterhead and signature for your convenience.

Remember, the letterhead is an extension of our professional identity. We are a successful firm and trial lawyers who correspond with insurers, judges, lawyers, courts, clients, etc. Make it new, modern, attractive, yet powerful and conservative.

It needs to be easily printable. I would like the bleed removed in print so the black bar the bottom crosses the page (but the text is not near the edges)
Updates

Low design quality

Target Market(s)

Clients, Government Offices, Judiciary, Lawyers, Insurance Companies, Colleagues.

Industry/Entity Type

Law

Other font styles liked:
• Segoe UI LIght, Calibri Light,

Colors
00AB8E
00BBA5
67D7C9
C6EFE9
E9F9F6

Requirements
Must have
• Everything that is on the letterhead now.
Nice to have
• Cutting Edge design, yet conservative.
Should not have
• law firm cliche design, images,

```html
<!DOCTYPE html>
<html lang="en">
<head>
<meta charset="utf-8">
<title>Corvelith Personal Injury Lawyers – Letterhead</title>
<link rel="stylesheet" href="https://fonts.googleapis.com/css2?family=Cinzel:wght@400&family=Open+Sans:wght@300;400&display=swap">
<style>
  :root {
    --brand-green: #8ec900;
    --brand-black: #111111;
    --paper: #ffffff;
    --backdrop: #d9d9d9;
    --watermark: #ececec;
    --watermark-rule: #f3f3f3;
    --text: #333333;
  }
  * { box-sizing: border-box; margin: 0; padding: 0; }
  html, body {
    width: 1200px;
    height: 848px;
    overflow: hidden;
    background: var(--backdrop);
  }
  .canvas {
    width: 1200px;
    height: 848px;
    display: flex;
    align-items: center;
    justify-content: center;
  }
  .letterhead {
    position: relative;
    width: 620px;
    height: 802px;
    background: var(--paper);
    box-shadow: 0 2px 10px rgba(0,0,0,0.18);
    overflow: hidden;
  }
  .watermark {
    position: absolute;
    left: 0;
    right: 0;
    top: 520px;
    text-align: center;
    font-family: "Cinzel", serif;
    color: var(--watermark);
    border-top: 1px solid var(--watermark-rule);
    border-bottom: 1px solid var(--watermark-rule);
  }
  .watermark-name {
    display: block;
    font-size: 92px;
    line-height: 1;
    letter-spacing: 2px;
    padding-top: 10px;
    border-bottom: 1px solid var(--watermark-rule);
  }
  .watermark-tagline {
    display: block;
    font-size: 31px;
    letter-spacing: 3px;
    line-height: 1;
    padding: 8px 0 10px;
  }
  .footer {
    position: absolute;
    right: 28px;
    bottom: 30px;
    display: flex;
    align-items: flex-end;
    gap: 18px;
  }
  .contact {
    font-family: "Open Sans", sans-serif;
    font-weight: 400;
    font-size: 8.5px;
    line-height: 1.45;
    color: var(--text);
    text-align: right;
  }
  .contact .dot {
    display: inline-block;
    width: 3px;
    height: 3px;
    margin: 0 3px 1px;
    background: var(--brand-green);
    vertical-align: middle;
  }
  .firm-mark {
    font-family: "Cinzel", serif;
    color: var(--brand-black);
    text-align: right;
    padding-bottom: 8px;
  }
  .firm-name {
    display: block;
    font-size: 24px;
    line-height: 1;
    letter-spacing: 0.5px;
  }
  .firm-tagline {
    display: block;
    font-size: 7px;
    letter-spacing: 1px;
    margin-top: 4px;
  }
  .bottom-bar {
    position: absolute;
    left: 0;
    right: 0;
    bottom: 0;
    height: 6px;
    display: flex;
  }
  .bottom-bar .bar-green { flex: 0 0 74%; background: var(--brand-green); }
  .bottom-bar .bar-black { flex: 1; background: var(--brand-black); }
</style>
</head>
<body>
  <main class="canvas">
    <article class="letterhead">
      <div class="watermark" aria-hidden="true">
        <span class="watermark-name">CORVELITH</span>
        <span class="watermark-tagline">PERSONAL INJURY LAWYERS</span>
      </div>

      <footer class="footer">
        <address class="contact">
          48 Harbour Road West, Suite 902, Eastbrook<br>
          ON K2V 3N8, Canada<span class="dot"></span>555-210-4477<br>
          info@corvelith.ca<span class="dot"></span>corvelith.ca
        </address>
        <div class="firm-mark">
          <span class="firm-name">CORVELITH</span>
          <span class="firm-tagline">PERSONAL INJURY LAWYERS</span>
        </div>
      </footer>

      <div class="bottom-bar">
        <span class="bar-green"></span>
        <span class="bar-black"></span>
      </div>
    </article>
  </main>
</body>
</html>
```